Trevani.com- International Goal Achievement Coach Needs Website Design

I need a web design for my new company called Trevani. I help people who are stuck, people who have a big dream, but don't know how to get there. I help them to break their dreams down into small, manageable steps... and then I'm the "kick in the shin" to get them moving and thriving!

We can all be better- We can all DO better. I inspire people to Go Boldly in the direction of your dreams.

I have uploaded my logo along with some vintage champagne posters. Please use the vintage posters as inspiration. I like the bold, vintage look and feel. I would love the main colors of the design to be black, white and metallic gold. And to follow along this vintage look and feel. Please feel free to use the logo in black or metallic gold or white.

Target Market(s)

websites that I like- lunabrask.com & tessak.tv

I would like to also use the vintage champagne photos attached as inspiration as well.

Industry/Entity Type

It Company

Requirements
Must have
• Tabs should include: About, Work With Me, Praise, Giving Back

On the homepage add:
* Sign up for newsletter with space to enter name and email (No click throughs)
* Upcoming Events/Sessions
* Newsletter Posts
* Resources
* Praise Section

* Large photo on top with additional photos throughout the page/site.
Nice to have
• Any additions you can bring to the table would be greatly appreciated.

```html
<!DOCTYPE html>
<html lang="en">
<head>
<meta charset="utf-8">
<title>Trevani — We Can All Do Better</title>
<link rel="stylesheet" href="https://fonts.googleapis.com/css2?family=Raleway:ital,wght@0,400;0,500;0,600;0,700;0,800;1,400;1,600&family=Josefin+Sans:wght@700&family=Yesteryear&display=swap">
<style>
  :root {
    --gold: #e6ab12;
    --gold-deep: #c48f08;
    --gold-soft: #f3c63a;
    --ink: #151515;
    --ink-2: #242424;
    --text: #6a6a6a;
    --text-dark: #2b2b2b;
    --line: #dcdad5;
    --paper: #f4f2ed;
    --white: #ffffff;
    --cyan: #1fc1d6;
    --icon-bg: #e4e4e4;
  }
  * { box-sizing: border-box; margin: 0; padding: 0; }
  html, body { width: 1200px; height: 2314px; overflow: hidden; background: var(--paper); }
  body { font-family: "Raleway", Arial, sans-serif; color: var(--text); }
  .page { position: relative; width: 1200px; height: 2314px; overflow: hidden;
    background: radial-gradient(ellipse at 40% 50%, #f7f6f2 0%, var(--paper) 70%, #efede7 100%); }
  .abs { position: absolute; }

  /* Brand */
  .brand { display: flex; align-items: center; gap: 8px; }
  .brand-dot { width: 34px; height: 34px; border-radius: 50%; background: var(--gold); }
  .brand-name { font-family: "Raleway", sans-serif; font-weight: 600; font-size: 18px; color: var(--gold); letter-spacing: .5px; }
  .brand.small .brand-dot { width: 26px; height: 26px; }
  .brand.small .brand-name { font-size: 14px; }

  /* Header */
  .site-header { left: 0; top: 0; width: 1200px; height: 58px;
    background: linear-gradient(#1d1d1d, #0e0e0e); border-bottom: 3px solid var(--gold); }
  .site-header .brand { position: absolute; left: 172px; top: 11px; }
  .main-nav { position: absolute; left: 559px; top: 21px; display: flex; gap: 50px; }
  .main-nav a { font-size: 12px; font-weight: 500; color: var(--gold); text-decoration: none; letter-spacing: .3px; }
  .search-icon { position: absolute; left: 994px; top: 20px; }

  /* Hero */
  .hero { left: 0; top: 61px; width: 1200px; height: 394px;
    background: radial-gradient(ellipse at 30% 40%, #f3f3f6 0%, #e2e3ea 55%, #d4d5de 100%);
    border-bottom: 3px solid var(--ink); }
  .hero-photo { position: absolute; left: 650px; top: 0; width: 450px; height: 394px;
    background: radial-gradient(ellipse at 55% 45%, #e8b9a2 0%, #c98f78 22%, #5a3a2e 48%, rgba(60,40,35,.85) 62%, rgba(220,222,230,0) 78%); }
  .hero-glass { position: absolute; left: 120px; top: 72px; width: 52px; height: 230px;
    background: linear-gradient(180deg, rgba(255,255,255,.7), rgba(230,215,170,.75) 50%, rgba(255,255,255,.4)); border-radius: 20px 20px 4px 4px; }
  .hero-script { position: absolute; left: 174px; top: 52px; font-family: "Yesteryear", cursive; font-size: 38px; color: var(--ink); }
  .hero-title { position: absolute; left: 174px; top: 100px; font-family: "Josefin Sans", sans-serif; font-weight: 700;
    font-size: 78px; line-height: 80px; letter-spacing: 2px; color: var(--white);
    -webkit-text-stroke: 2px var(--ink); text-shadow: 4px 4px 0 var(--ink); }
  .hero-rule { position: absolute; left: 174px; top: 274px; width: 464px; height: 3px; background: var(--ink); }
  .hero-signup { position: absolute; left: 174px; top: 285px; font-size: 12px; color: var(--ink); }
  .hero-signup strong { font-weight: 800; font-size: 14px; }
  .hero-free { position: absolute; left: 174px; top: 304px; font-size: 18px; font-weight: 800; color: var(--gold); letter-spacing: .5px; }
  .signup-form { position: absolute; left: 174px; top: 337px; display: flex; gap: 7px; }
  .field { height: 30px; background: var(--white); border: 1px solid #cfcfcf; font-size: 12px; color: #555; padding: 0 12px; display: flex; align-items: center; }
  .btn-dark { height: 30px; background: linear-gradient(#3a3a3a, #101010); color: var(--white); font-size: 10px; font-weight: 600;
    display: flex; align-items: center; justify-content: center; border-radius: 2px; letter-spacing: .3px; }

  /* Main column */
  .feature-title { left: 172px; top: 494px; font-size: 30px; font-weight: 700; color: var(--gold); }
  .body-copy { font-size: 12.5px; line-height: 17.6px; color: var(--text); }
  .feature-copy { left: 172px; top: 540px; width: 598px; }
  .divider { height: 1px; background: var(--line); }
  .related-heading { left: 172px; top: 765px; font-size: 11.5px; font-weight: 700; color: var(--text-dark); }
  .related { left: 172px; top: 790px; display: flex; gap: 3px; }
  .related-item { width: 197px; }
  .thumb { width: 197px; height: 114px; }
  .related-item p { font-size: 12.5px; line-height: 17px; color: var(--text-dark); margin-top: 8px; }
  .related-item p.hl { color: var(--gold); font-weight: 600; }
  .related-item .view { display: block; font-size: 10px; color: var(--text-dark); text-decoration: underline; margin-top: 1px; }

  .actions { display: flex; gap: 8px; }
  .act { position: relative; width: 28px; height: 26px; background: var(--icon-bg); border: 1px solid #d3d3d3; display: flex; align-items: center; justify-content: center; }
  .badge { position: absolute; right: -8px; top: -9px; width: 17px; height: 17px; border-radius: 50%; background: var(--cyan); color: var(--white); font-size: 9px; font-weight: 700; display: flex; align-items: center; justify-content: center; }
  .read-more { font-size: 11.5px; color: var(--text-dark); }

  .post-card { left: 172px; width: 598px; background: var(--white); border: 1px solid #dedbd5; }
  .post-media { position: relative; height: 268px; border: 1px solid #b02a22;
    background: linear-gradient(100deg, #c8262a 0%, #e8c59a 22%, #d9b07a 40%, #eedcc0 55%, #c4583a 75%, #e8d6c0 100%); }
  .post-band { position: absolute; left: 0; bottom: 0; width: 100%; height: 73px; background: rgba(40,34,28,.62); display: flex; align-items: center; justify-content: space-between; padding: 0 28px 0 18px; }
  .post-band h2 { font-size: 24px; font-weight: 600; color: var(--gold-soft); letter-spacing: .3px; }
  .post-meta { position: absolute; left: 18px; top: 281px; font-size: 9.5px; color: #555; font-style: italic; }
  .post-meta b { font-weight: 600; color: var(--text-dark); }
  .post-copy { position: absolute; left: 18px; top: 300px; width: 560px; }
  .post-actions { position: absolute; left: 18px; top: 443px; }
  .post-read { position: absolute; right: 16px; top: 455px; }

  .load-more { left: 301px; top: 2061px; width: 339px; height: 42px; background: var(--white); border: 1px solid #e0ded9;
    display: flex; align-items: center; justify-content: center; gap: 10px; font-size: 11.5px; font-weight: 700; letter-spacing: 1.5px; color: var(--text-dark); }

  /* Sidebar */
  .side-label { font-size: 12px; font-weight: 700; color: var(--text-dark); letter-spacing: .3px; }
  .social-label { left: 790px; top: 500px; font-size: 11px; font-weight: 700; color: var(--gold); }
  .social-row { display: flex; gap: 3px; }
  .social-row span { width: 28px; height: 28px; border-radius: 3px; }
  .ad { left: 790px; width: 238px; overflow: hidden; }
  .ad-light { top: 574px; height: 137px; background: linear-gradient(90deg, #e9e9f1 0%, #dcdbe8 50%, #c9a796 75%, #dcdce6 100%); }
  .ad-light p { position: absolute; left: 12px; top: 10px; width: 120px; font-size: 10.5px; line-height: 14px; color: #7a7a86; }
  .ad-light .brand { position: absolute; left: 12px; bottom: 12px; }
  .ad-yellow { top: 722px; height: 273px; background: radial-gradient(ellipse at 55% 35%, #f1d7a8 0%, #d9a12a 40%, #b98812 70%, #8d6b0c 100%); }
  .ad-yellow .band { position: absolute; left: 0; bottom: 0; width: 100%; height: 78px; background: rgba(45,38,20,.72); padding: 12px 12px; }
  .ad-yellow .band p { font-size: 14px; line-height: 17px; font-weight: 600; color: var(--gold-soft); width: 150px; }
  .ad-yellow .band .brand { position: absolute; right: 10px; top: 24px; }
  .ad-yellow .top-mark { position: absolute; left: 10px; top: 10px; }
  .ad-dark { top: 1007px; height: 198px; background: linear-gradient(90deg, #6d5308 0%, #a88114 35%, #3c2a10 65%, #8a6a14 100%); }
  .ad-dark .brand { position: absolute; left: 12px; top: 14px; }
  .ad-dark p { position: absolute; left: 18px; top: 78px; font-size: 14.5px; line-height: 19px; font-weight: 600; color: var(--gold-soft); width: 100px; }

  .popular-title { left: 790px; top: 1232px; }
  .popular { left: 790px; top: 1263px; width: 238px; }
  .pop-item { display: flex; gap: 12px; height: 94px; }
  .pop-thumb { width: 84px; height: 83px; flex: none; }
  .pop-item h3 { font-size: 10px; line-height: 14px; font-weight: 600; color: var(--text-dark); margin-top: 4px; }
  .pop-item time { display: block; font-size: 9.5px; color: #9a9a9a; margin-top: 18px; }
  .pop-item .txt { border-bottom: 1px solid var(--line); height: 83px; flex: 1; }

  .video-title { left: 790px; top: 1658px; }
  .video { left: 790px; top: 1683px; width: 238px; height: 125px;
    background: linear-gradient(90deg, #e8a20a 0%, #f2b622 35%, #d08a10 60%, #3a2a16 80%, #1d1812 100%); }
  .video svg { position: absolute; left: 105px; top: 47px; }

  .comments-title { left: 790px; top: 1837px; }
  .comments { left: 793px; top: 1870px; }
  .comments li { list-style: none; display: flex; align-items: center; gap: 6px; height: 28px; font-size: 10px; color: #9a9a9a; }

  /* Footer */
  .site-footer { left: 0; top: 2114px; width: 1200px; height: 200px; background: linear-gradient(#131313, #0a0a0a); border-top: 1px solid #000; }
  .foot-nav { position: absolute; left: 172px; top: 28px; display: flex; gap: 44px; }
  .foot-nav a { font-size: 11.5px; color: #c8c8c8; text-decoration: none; letter-spacing: .3px; }
  .foot-nav a.current { color: var(--gold); }
  .site-footer .brand { position: absolute; left: 925px; top: 17px; }
  .foot-label { position: absolute; top: 90px; font-size: 11.5px; color: #bdbdbd; letter-spacing: .3px; }
  .foot-form { position: absolute; left: 172px; top: 120px; display: flex; gap: 7px; }
  .foot-social { position: absolute; left: 790px; top: 120px; }
  .foot-social span { background: #6e6e6e; }
</style>
</head>
<body>
<div class="page">

  <header class="site-header abs">
    <div class="brand"><span class="brand-dot"></span><span class="brand-name">Trevani</span></div>
    <nav class="main-nav">
      <a href="#">ABOUT</a><a href="#">WORK WITH ME</a><a href="#">PRAISE</a><a href="#">GIVING BACK</a>
    </nav>
    <svg class="search-icon" width="16" height="16" viewBox="0 0 16 16"><circle cx="6.5" cy="6.5" r="5" fill="none" stroke="#e6ab12" stroke-width="1.6"/><line x1="10.2" y1="10.2" x2="14.5" y2="14.5" stroke="#e6ab12" stroke-width="1.8"/></svg>
  </header>

  <section class="hero abs">
    <div class="hero-photo" role="img" aria-label="Photo of a laughing woman raising her arm in celebration"></div>
    <div class="hero-glass" role="img" aria-label="Photo of a raised champagne glass"></div>
    <div class="hero-script">We can all be better.</div>
    <h1 class="hero-title">WE CAN ALL<br>DO BETTER.</h1>
    <div class="hero-rule"></div>
    <p class="hero-signup"><strong>SIGN UP FOR TREVANI Newsletter</strong> and Go Boldly In The Direction Of Their Dreams...</p>
    <p class="hero-free">IT'S FREE</p>
    <div class="signup-form">
      <div class="field" style="width:183px">First name</div>
      <div class="field" style="width:181px">Email</div>
      <div class="btn-dark" style="width:86px">SUBSCRIBE</div>
    </div>
  </section>

  <!-- Feature article -->
  <h2 class="feature-title abs">THE No.1 KEY TO SUCCESS</h2>
  <p class="feature-copy body-copy abs">Suspendisse blandit ligula turpis, ac convallis risus fermentum non. Duis vestibulum quis quam vel accumsan. Nunc a vulputate lectus. Vestibulum eleifend nisl sed massa sagittis vestibulum. Vestibulum pretium blandit tellus, sodales volutpat sapien varius vel. Phasellus tristique cursus erat, a placerat tellus laoreet eget. Fusce vitae dui sit amet lacus rutrum convallis. Vivamus sit amet lectus venenatis est rhoncus interdum a vitae velit.<br>Suspendisse blandit ligula turpis, ac convallis risus fermentum non. Duis vestibulum quis quam vel accumsan. Nunc a vulputate lectus. Vestibulum eleifend nisl sed massa sagittis vestibulum. Vestibulum pretium blandit tellus, sodales volutpat sapien varius vel. Phasellus tristique cursus erat, a placerat tellus laoreet eget. Fusce vitae dui sit amet lacus rutrum convallis. Vivamus sit amet lectus venenatis est rhoncus interdum a vitae velit.</p>
  <div class="divider abs" style="left:172px;top:740px;width:598px"></div>
  <h3 class="related-heading abs">IN ADDITION TO PRACTICING THE #1 KEY TO SUCCESS, YOU MAY ALSO LIKE THESE POSTS:</h3>
  <div class="related abs">
    <div class="related-item">
      <div class="thumb" role="img" aria-label="Photo of a woman seated in a mountain landscape" style="background:linear-gradient(180deg,#c9cfd6 0%,#a9a59a 55%,#8a7658 100%)"></div>
      <p>The #1 Key to Manifesting</p>
    </div>
    <div class="related-item">
      <div class="thumb" role="img" aria-label="Photo of a smiling woman lying in green grass" style="background:radial-gradient(ellipse at 50% 50%,#e6c07a 0%,#a9b424 45%,#6f8f12 100%)"></div>
      <p class="hl">How to handle success.</p>
      <a class="view">View Post</a>
    </div>
    <div class="related-item">
      <div class="thumb" role="img" aria-label="Portrait photo of a smiling woman" style="background:linear-gradient(90deg,#e6e7ea 0%,#cfc9c6 40%,#6b4a3a 60%,#dcdde0 100%)"></div>
      <p>Reclaim your power when you feel powerless.</p>
    </div>
  </div>
  <div class="actions abs" style="left:172px;top:987px">
    <div class="act"><svg width="13" height="12" viewBox="0 0 13 12"><path d="M1 1h11v7H5l-3 3V8H1z" fill="#666"/></svg><span class="badge">6</span></div>
    <div class="act"><svg width="13" height="13" viewBox="0 0 13 13"><circle cx="10" cy="2.5" r="2" fill="#666"/><circle cx="3" cy="6.5" r="2" fill="#666"/><circle cx="10" cy="10.5" r="2" fill="#666"/><path d="M10 2.5L3 6.5l7 4" fill="none" stroke="#666" stroke-width="1.2"/></svg></div>
  </div>
  <span class="read-more abs" style="left:699px;top:998px">&gt; Read More</span>
  <div class="divider abs" style="left:172px;top:1027px;width:598px"></div>

  <!-- Post 1 -->
  <article class="post-card abs" style="top:1048px;height:488px">
    <div class="post-media" role="img" aria-label="Photo of three smiling women in sunglasses on a sunny street">
      <div class="post-band"><h2>SEMPER AT EGESTAS SED...</h2><div class="brand small"><span class="brand-dot"></span><span class="brand-name">Trevani</span></div></div>
    </div>
    <p class="post-meta">By <b>Marcus Ellery</b> Business, <b>Education, Health</b> Posted <b>May 24, 2013</b></p>
    <p class="post-copy body-copy">Suspendisse blandit ligula turpis, ac convallis risus fermentum non. Duis vestibulum quis quam vel accumsan. Nunc a vulputate lectus. Vestibulum eleifend nisl sed massa sagittis vestibulum. Vestibulum pretium blandit tellus, sodales volutpat sapien varius vel. Phasellus tristique cursus erat, a placerat tellus laoreet eget. Fusce vitae dui sit amet lacus rutrum convallis. Vivamus sit amet lectus venenatis est rhoncus interdum a vitae velit.</p>
    <div class="post-actions actions">
      <div class="act"><svg width="13" height="12" viewBox="0 0 13 12"><path d="M1 1h11v7H5l-3 3V8H1z" fill="#666"/></svg><span class="badge">6</span></div>
      <div class="act"><svg width="13" height="13" viewBox="0 0 13 13"><circle cx="10" cy="2.5" r="2" fill="#666"/><circle cx="3" cy="6.5" r="2" fill="#666"/><circle cx="10" cy="10.5" r="2" fill="#666"/><path d="M10 2.5L3 6.5l7 4" fill="none" stroke="#666" stroke-width="1.2"/></svg></div>
    </div>
    <span class="post-read read-more">&gt; Read More</span>
  </article>

  <!-- Post 2 -->
  <article class="post-card abs" style="top:1564px;height:486px">
    <div class="post-media" role="img" aria-label="Photo of three smiling women in sunglasses on a sunny street">
      <div class="post-band"><h2>SEMPER AT EGESTAS SED...</h2><div class="brand small"><span class="brand-dot"></span><span class="brand-name">Trevani</span></div></div>
    </div>
    <p class="post-meta">By <b>Marcus Ellery</b> Business, <b>Education, Health</b> Posted <b>May 24, 2013</b></p>
    <p class="post-copy body-copy">Suspendisse blandit ligula turpis, ac convallis risus fermentum non. Duis vestibulum quis quam vel accumsan. Nunc a vulputate lectus. Vestibulum eleifend nisl sed massa sagittis vestibulum. Vestibulum pretium blandit tellus, sodales volutpat sapien varius vel. Phasellus tristique cursus erat, a placerat tellus laoreet eget. Fusce vitae dui sit amet lacus rutrum convallis. Vivamus sit amet lectus venenatis est rhoncus interdum a vitae velit.</p>
    <div class="post-actions actions">
      <div class="act"><svg width="13" height="12" viewBox="0 0 13 12"><path d="M1 1h11v7H5l-3 3V8H1z" fill="#666"/></svg><span class="badge">6</span></div>
      <div class="act"><svg width="13" height="13" viewBox="0 0 13 13"><circle cx="10" cy="2.5" r="2" fill="#666"/><circle cx="3" cy="6.5" r="2" fill="#666"/><circle cx="10" cy="10.5" r="2" fill="#666"/><path d="M10 2.5L3 6.5l7 4" fill="none" stroke="#666" stroke-width="1.2"/></svg></div>
    </div>
    <span class="post-read read-more">&gt; Read More</span>
  </article>

  <div class="load-more abs">
    <svg width="10" height="13" viewBox="0 0 10 13"><path d="M5 0v11M1 7l4 4 4-4" fill="none" stroke="#777" stroke-width="1.4"/></svg>
    LOAD MORE
  </div>

  <!-- Sidebar -->
  <p class="social-label abs">SOCIAL MEDIA :</p>
  <div class="social-row abs" style="left:790px;top:521px">
    <span style="background:#3b5a9a"></span><span style="background:#37a9e1"></span><span style="background:#e8762b"></span><span style="background:#d64937"></span><span style="background:#1ab7ea"></span><span style="background:#c8232c"></span><span style="background:#0e76a8"></span><span style="background:#517fa4"></span>
  </div>

  <div class="ad ad-light abs" role="img" aria-label="Promo with photo of a laughing woman holding a champagne glass">
    <p>Reclaim your power when you feel powerless.</p>
    <div class="brand small"><span class="brand-dot"></span><span class="brand-name">Trevani</span></div>
  </div>
  <div class="ad ad-yellow abs" role="img" aria-label="Promo with photo of a smiling blonde woman in warm light">
    <div class="top-mark brand small"><span class="brand-dot"></span></div>
    <div class="band"><p>RECLAIM YOUR POWER WHEN YOU FEEL POWERLESS.</p><div class="brand small"><span class="brand-name">Trevani</span></div></div>
  </div>
  <div class="ad ad-dark abs" role="img" aria-label="Promo with photo of a woman in a vintage hat and pearls">
    <div class="brand small"><span class="brand-dot"></span><span class="brand-name">Trevani</span></div>
    <p>RECLAIM YOUR POWER WHEN YOU FEEL POWERLESS.</p>
  </div>

  <h3 class="popular-title side-label abs">POPULAR POSTS</h3>
  <div class="popular abs">
    <div class="pop-item"><div class="pop-thumb" role="img" aria-label="Portrait photo of a smiling woman" style="background:linear-gradient(90deg,#e3e3e6,#b08a76 55%,#4a3428)"></div><div class="txt"><h3>SEMPER AT EGESTAS SED, ELEMENTUM IN JUSTO</h3><time>May 24, 2013</time></div></div>
    <div class="pop-item"><div class="pop-thumb" role="img" aria-label="Photo of a woman seated in a mountain landscape" style="background:linear-gradient(180deg,#cdd2d8,#a7a193 55%,#87714f)"></div><div class="txt"><h3>SEMPER AT EGESTAS SED, ELEMENTUM IN JUSTO</h3><time>May 24, 2013</time></div></div>
    <div class="pop-item"><div class="pop-thumb" role="img" aria-label="Photo of a laughing woman raising her arm" style="background:linear-gradient(90deg,#e6e7ec,#c99683 50%,#3d2a24)"></div><div class="txt"><h3>SEMPER AT EGESTAS SED, ELEMENTUM IN JUSTO</h3><time>May 24, 2013</time></div></div>
    <div class="pop-item"><div class="pop-thumb" role="img" aria-label="Dramatic portrait photo in black, white and red" style="background:linear-gradient(135deg,#111,#3a3a3a 40%,#b61d24 60%,#e8e8e8)"></div><div class="txt"><h3>SEMPER AT EGESTAS SED, ELEMENTUM IN JUSTO</h3><time>May 24, 2013</time></div></div>
  </div>

  <h3 class="video-title side-label abs">VIDEO</h3>
  <div class="video abs" role="img" aria-label="Video still of a businessman offering a handshake">
    <svg width="30" height="30" viewBox="0 0 30 30"><circle cx="15" cy="15" r="13" fill="none" stroke="#6a4a06" stroke-width="2.5"/><path d="M12 9.5l8 5.5-8 5.5z" fill="#6a4a06"/></svg>
  </div>

  <h3 class="comments-title side-label abs">RECENT COMMENTS</h3>
  <ul class="comments abs">
    <li><svg width="9" height="8" viewBox="0 0 9 8"><path d="M0 0h9v5H4L2 8V5H0z" fill="#aaa"/></svg>Admin On Proin Et Dignissim Magna</li>
    <li><svg width="9" height="8" viewBox="0 0 9 8"><path d="M0 0h9v5H4L2 8V5H0z" fill="#aaa"/></svg>Admin On Proin Et Dignissim Magna</li>
    <li><svg width="9" height="8" viewBox="0 0 9 8"><path d="M0 0h9v5H4L2 8V5H0z" fill="#aaa"/></svg>Admin On Proin Et Dignissim Magna</li>
    <li><svg width="9" height="8" viewBox="0 0 9 8"><path d="M0 0h9v5H4L2 8V5H0z" fill="#aaa"/></svg>Admin On Proin Et Dignissim Magna</li>
  </ul>

  <!-- Footer -->
  <footer class="site-footer abs">
    <nav class="foot-nav">
      <a class="current" href="#">HOME</a><a href="#">ABOUT</a><a href="#">WORK WITH ME</a><a href="#">PRAISE</a><a href="#">GIVING BACK</a><a href="#">PRIVACY POLICY</a><a href="#">SITEMAP</a>
    </nav>
    <div class="brand"><span class="brand-dot"></span><span class="brand-name">Trevani</span></div>
    <p class="foot-label" style="left:172px">NEWSLETTER SUBSCRIPTION:</p>
    <p class="foot-label" style="left:790px">SOCIAL MEDIA:</p>
    <div class="foot-form">
      <div class="field" style="width:183px">First name</div>
      <div class="field" style="width:186px">Email</div>
      <div class="btn-dark" style="width:86px">SUBSCRIBE</div>
    </div>
    <div class="foot-social social-row">
      <span></span><span></span><span></span><span></span><span></span><span></span><span></span><span></span>
    </div>
  </footer>

</div>
</body>
</html>
```